Packaging design for a reclosable bag for our product

We have a logo, and we need to put it on packaging for our product and while we want the look to be simple, we want it to follow good design principles and also contain spaces for other product descriptions.

There will be 5 sizes at launch so I'd like 5 variations, one for each size.

I've included a few mockups of the type of bag that I made but they are all just rough ideas that I had.

I want the brand to look scientific and methodical and even a bit quirky, as in "wow this is a serious product but also a bit unusual."

```html
<!DOCTYPE html>
<html lang="en">
<head>
<meta charset="utf-8">
<title>HV7 Bias Lighting Pouch</title>
<link rel="stylesheet" href="https://fonts.googleapis.com/css2?family=Barlow:wght@500;600;700&family=Barlow+Condensed:wght@600;700&family=Barlow+Semi+Condensed:wght@800&display=swap">
<style>
  :root {
    --stage: #2f3034;
    --pouch: #f4f4f4;
    --ink: #111113;
    --pattern-light: #ececee;
    --pattern-mid: #dcdcdf;
    --pattern-dark: #cfcfd3;
    --pill-start: #1a1a1c;
    --pill-end: #8a8a8e;
    --badge: #ffffff;
  }
  * { margin: 0; padding: 0; box-sizing: border-box; }
  html, body {
    width: 1200px; height: 833px; overflow: hidden;
    background: var(--stage);
  }
  .canvas {
    position: relative; width: 1200px; height: 833px;
    background: var(--stage);
  }
  .pouch-front {
    position: absolute; left: 355px; top: 108px;
    width: 490px; height: 644px;
    background: var(--pouch);
    overflow: hidden;
    font-family: "Barlow", sans-serif;
    color: var(--ink);
  }
  .pattern {
    position: absolute; inset: 0; width: 100%; height: 100%;
  }
  .size-badge {
    position: absolute; left: 48px; top: 78px;
    width: 58px; height: 58px; border-radius: 50%;
    background: var(--badge);
    display: flex; flex-direction: column; align-items: center; justify-content: center;
    font-family: "Barlow Condensed", sans-serif; font-weight: 700;
  }
  .size-badge .value { font-size: 25px; line-height: 0.95; }
  .size-badge .unit { font-size: 8px; letter-spacing: 0.3px; font-family: "Barlow", sans-serif; font-weight: 600; }
  .category {
    position: absolute; left: 117px; top: 180px; width: 270px;
    font-size: 28px; font-weight: 700; letter-spacing: 3.4px; line-height: 30px;
    white-space: nowrap;
  }
  .variant-bar {
    position: absolute; left: 117px; top: 212px;
    width: 258px; height: 22px; border-radius: 11px;
    background: var(--ink); color: var(--pouch);
    font-size: 10px; font-weight: 500; letter-spacing: 7px;
    display: flex; align-items: center; justify-content: center;
    padding-left: 7px;
  }
  .brand-name {
    position: absolute; left: 45px; top: 224px; width: 400px;
    font-family: "Barlow Semi Condensed", sans-serif;
    font-size: 240px; font-weight: 800; line-height: 1;
    letter-spacing: -14px; text-align: center;
  }
  .spec-pill {
    position: absolute; left: 115px; top: 467px;
    width: 257px; height: 44px; border-radius: 22px;
    background: linear-gradient(90deg, var(--pill-start) 0%, var(--pill-start) 35%, var(--pill-end) 100%);
    color: #ffffff;
    display: flex; align-items: center; gap: 8px; padding-left: 14px;
    font-family: "Barlow Condensed", sans-serif; font-weight: 700; font-size: 19px;
  }
  .spec-pill svg { width: 18px; height: 18px; flex: none; }
  .temperature {
    position: absolute; right: 88px; top: 580px; text-align: center;
  }
  .temperature .kelvin {
    display: block; font-family: "Barlow Condensed", sans-serif;
    font-weight: 700; font-size: 40px; line-height: 1;
  }
  .temperature .caption {
    display: block; font-size: 8px; font-weight: 500; letter-spacing: 0.1px;
  }
</style>
</head>
<body>
<main class="canvas">
  <section class="pouch-front">
    <svg class="pattern" viewBox="0 0 490 644" role="img" aria-label="Fine curved line pattern sweeping across the top and lower left of the pouch">
      <defs>
        <linearGradient id="sweep-top" x1="0" y1="0" x2="1" y2="0.6">
          <stop offset="0" stop-color="var(--pattern-dark)"/>
          <stop offset="0.6" stop-color="var(--pattern-mid)"/>
          <stop offset="1" stop-color="var(--pattern-light)"/>
        </linearGradient>
        <linearGradient id="sweep-bottom" x1="0" y1="1" x2="1" y2="0.4">
          <stop offset="0" stop-color="var(--pattern-dark)"/>
          <stop offset="0.6" stop-color="var(--pattern-mid)"/>
          <stop offset="1" stop-color="var(--pattern-light)"/>
        </linearGradient>
      </defs>
      <path d="M0 0 H490 V105 C420 62 310 52 210 82 C120 110 45 175 0 250 Z" fill="url(#sweep-top)"/>
      <path d="M0 500 C55 575 150 600 250 612 C330 622 410 636 490 644 H0 Z" fill="url(#sweep-bottom)"/>
      <path d="M490 440 C470 500 440 545 405 575 C440 600 470 620 490 630 Z" fill="url(#sweep-bottom)"/>
    </svg>

    <div class="size-badge">
      <span class="value">5</span>
      <span class="unit">METERS</span>
    </div>

    <h2 class="category">BIAS LIGHTING</h2>
    <div class="variant-bar">EXTRA LARGUE</div>

    <h1 class="brand-name">HV7</h1>

    <div class="spec-pill">
      <svg viewBox="0 0 20 20" fill="none" stroke="#fff" stroke-width="1.4">
        <circle cx="10" cy="10" r="4"/>
        <path d="M10 1v3M10 16v3M1 10h3M16 10h3M3.6 3.6l2.1 2.1M14.3 14.3l2.1 2.1M3.6 16.4l2.1-2.1M14.3 5.7l2.1-2.1"/>
      </svg>
      SIMULATED D65 CRI 90+
    </div>

    <div class="temperature">
      <span class="kelvin">6500K</span>
      <span class="caption">WHITE BIAS LIGHTING</span>
    </div>
  </section>
</main>
</body>
</html>
```